Business card design needed

I would like a one sided black business card with the information provided above. Refer to my website www.brightvolleyracquets.com.au for an example of colors I have used for my site, would like to keep this consistent for my business cards also, I will upload my logo below.

I am a new small business that provides tennis customers with racquet re stringing, tennis strings and accessories.

Industry/Entity Type

Small Business

Contact Information for Business Card

Bright Volley Tennis

Owen Whitby
Managing Director

brightvolleyracquets@mailbox.example
www.brightvolleyracquets.com.au
0491 726 305

Racquet Restringing/Tennis Strings/Accessories

Requirements
Must have
• Must have my logo and card must be black

```html
<!DOCTYPE html>
<html lang="en">
<head>
<meta charset="utf-8">
<title>Bright Volley Tennis – Business Card</title>
<link rel="stylesheet" href="https://fonts.googleapis.com/css2?family=Open+Sans:ital,wght@0,400;0,700;1,700&display=swap">
<style>
  :root {
    --backdrop: #d9d6d2;
    --card-black: #000000;
    --lime: #b8d432;
    --court-blue: #215186;
    --white: #ffffff;
  }
  * { margin: 0; padding: 0; box-sizing: border-box; }
  html, body {
    width: 1200px;
    height: 750px;
    overflow: hidden;
    background: var(--backdrop);
    font-family: "Open Sans", Arial, sans-serif;
  }
  .card {
    position: absolute;
    left: 75px;
    top: 75px;
    width: 1050px;
    height: 600px;
    background: var(--card-black);
    border-radius: 32px;
    overflow: hidden;
    color: var(--white);
    text-align: center;
  }
  .brand {
    position: absolute;
    left: 0;
    right: 0;
    top: 118px;
    display: flex;
    justify-content: center;
    align-items: center;
    gap: 20px;
  }
  .brand-dot {
    width: 54px;
    height: 54px;
    border-radius: 50%;
    background: var(--lime);
  }
  .brand-name {
    font-size: 60px;
    font-weight: 700;
    color: var(--lime);
    line-height: 1;
  }
  .contact {
    position: absolute;
    left: 0;
    right: 0;
    top: 318px;
    font-size: 25px;
    line-height: 39px;
  }
  .person { color: var(--lime); margin-bottom: 2px; }
  .person-name { font-size: 30px; font-weight: 700; }
  .person-title { font-size: 25px; }
  .label { font-weight: 700; font-style: italic; }
  .services {
    position: absolute;
    left: 0;
    right: 0;
    top: 505px;
    font-size: 25px;
    display: flex;
    justify-content: center;
    gap: 12px;
  }
  .service::before {
    content: "";
    display: inline-block;
    width: 8px;
    height: 8px;
    background: var(--white);
    margin-right: 9px;
    vertical-align: 5px;
  }
  .base-band {
    position: absolute;
    left: 0;
    bottom: 0;
    width: 1050px;
    height: 48px;
    display: block;
  }
</style>
</head>
<body>
  <main class="card">
    <div class="brand">
      <span class="brand-dot"></span>
      <span class="brand-name">Bright Volley Tennis</span>
    </div>

    <div class="contact">
      <p class="person"><span class="person-name">Owen Whitby,</span> <span class="person-title">Managing Director</span></p>
      <p><span class="label">phone</span> 0491 726 305</p>
      <p><span class="label">email</span> brightvolleyracquets@mailbox.example</p>
      <p><span class="label">web</span> www.brightvolleyracquets.com.au</p>
    </div>

    <div class="services">
      <span class="service">Racquet Restringing</span>
      <span class="service">Tennis Strings</span>
      <span class="service">Accessories</span>
    </div>

    <svg class="base-band" viewBox="0 0 1050 48" aria-hidden="true">
      <rect x="0" y="0" width="1050" height="48" fill="var(--lime)"/>
      <polygon points="0,0 468,0 510,48 0,48" fill="var(--court-blue)"/>
    </svg>
  </main>
</body>
</html>
```